Velmora Freightway Solutions Business cards

Would like a very unique design catchy but professional for business cards. Please use log provided.Marlon WellsCeo and Founder TransCon Logistix Solutions1-888-913-3225mwells@tlsolutionsus.comwww.tlsolutionsus.com

```html
<!DOCTYPE html>
<html lang="en">
<head>
<meta charset="utf-8">
<title>Velmora Freightway Solutions – Business Cards</title>
<link rel="stylesheet" href="https://fonts.googleapis.com/css2?family=Lato:wght@400;700&display=swap">
<style>
  :root {
    --brand-blue: #1a6fbb;
    --brand-red: #e3222b;
    --navy: #0d2a47;
    --text-dark: #2b2b2b;
    --card-white: #ffffff;
    --backdrop: #e6e7e9;
  }
  * { margin: 0; padding: 0; box-sizing: border-box; }
  html, body { width: 1200px; height: 960px; overflow: hidden; }
  body {
    background: var(--backdrop);
    font-family: "Lato", Arial, sans-serif;
    position: relative;
  }
  .card {
    position: absolute;
    background: var(--card-white);
    border-radius: 30px;
    overflow: hidden;
  }
  .card--front { left: 237px; top: 47px; width: 721px; height: 406px; }
  .card--back  { left: 245px; top: 508px; width: 705px; height: 407px; }

  .front-name {
    position: absolute;
    left: 0; right: 0; top: 150px;
    text-align: center;
    color: var(--brand-blue);
    font-weight: 700;
    font-size: 42px;
    line-height: 1.15;
    letter-spacing: 2px;
    text-transform: uppercase;
  }
  .front-web {
    position: absolute;
    left: 0; right: 0; top: 357px;
    display: flex; align-items: center; justify-content: center; gap: 12px;
    font-size: 16px; letter-spacing: 2.5px; color: var(--text-dark);
  }
  .front-web::before, .front-web::after {
    content: ""; width: 90px; height: 3px; background: var(--brand-blue); border-radius: 2px;
  }

  .back-name {
    position: absolute;
    left: 40px; width: 340px; top: 150px;
    text-align: center;
    color: var(--brand-blue);
    font-weight: 700;
    font-size: 23px;
    line-height: 1.2;
    letter-spacing: 1px;
    text-transform: uppercase;
  }
  .divider {
    position: absolute; left: 387px; top: 72px; width: 1px; height: 218px;
    background: #c9c9c9;
  }
  .contact { position: absolute; left: 409px; top: 68px; color: var(--text-dark); }
  .person-name { color: var(--brand-blue); font-weight: 700; font-size: 24px; }
  .person-title { color: var(--brand-red); font-size: 18px; margin-top: 6px; text-transform: uppercase; }
  .address { font-size: 17px; line-height: 27px; margin-top: 16px; }
  .contact-list { list-style: none; margin-top: 16px; font-size: 17px; }
  .contact-list li { display: flex; align-items: center; gap: 10px; height: 30px; }
  .contact-list svg { width: 16px; height: 16px; fill: var(--brand-blue); flex: none; }
  .swoosh { position: absolute; left: 0; top: 0; width: 705px; height: 407px; }
</style>
</head>
<body>
  <section class="card card--front">
    <h1 class="front-name">Velmora Freightway<br>Solutions</h1>
    <p class="front-web">www.vfwayroutes.com</p>
  </section>

  <section class="card card--back">
    <svg class="swoosh" viewBox="0 0 705 407" aria-hidden="true">
      <path d="M0,277 Q300,318 560,377 L520,380 Q260,335 0,322 Z" fill="var(--brand-blue)"/>
      <path d="M0,330 Q330,338 625,372 L545,407 L0,407 Z" fill="var(--navy)"/>
      <path d="M0,326 Q330,334 625,372" fill="none" stroke="#fff" stroke-width="3"/>
      <path d="M545,407 Q640,385 705,347 L705,407 Z" fill="var(--brand-blue)"/>
    </svg>
    <p class="back-name">Velmora Freightway<br>Solutions</p>
    <div class="divider"></div>
    <div class="contact">
      <h2 class="person-name">DORIAN PIKE</h2>
      <p class="person-title">CEO and Founder</p>
      <p class="address">2740 Harlow Creek Rd<br>Atlanta, GA 30327</p>
      <ul class="contact-list">
        <li><svg viewBox="0 0 16 16"><path d="M4 1 L6.5 4.5 L5 6 Q6.5 9.5 10 11 L11.5 9.5 L15 12 L13 15 Q4 13 1 3 Z"/></svg>1-888-470-6158</li>
        <li><svg viewBox="0 0 16 16"><path d="M1 4 H15 V13 H1 Z M1 4 L8 9 L15 4" stroke="#fff" stroke-width="1"/></svg>dpike@vfwayroutes.com</li>
        <li><svg viewBox="0 0 16 16"><circle cx="8" cy="8" r="6.5" fill="none" stroke="var(--brand-blue)" stroke-width="1.3"/><path d="M1.5 8 H14.5 M8 1.5 Q4 8 8 14.5 M8 1.5 Q12 8 8 14.5" fill="none" stroke="var(--brand-blue)" stroke-width="1.1"/></svg>www.vfwayroutes.com</li>
      </ul>
    </div>
  </section>
</body>
</html>
```